Catering Menu Package

I currently have a complete menu package, which we have redesigned as far as content, now I need to it put together in a catalog type format. It is essentially 10-12 pages in length, and will be sent for print production. Upon receiving a final edit
Updates

I have added an example gif to the project.

I did this free hand this basically what I am looking for. please change text and type to whatever you think would look best. This is a total rough design so, feel free to change any and everything. The text for the page is on the word documents. If you need more images let me know I am in the process of getting as many images uploaded for your use.

Project Deadline Extended
Reason: I figured we got a late jump with questions, so i am extending a few days .

Target Market(s)

The target market is business who wish to have catered luncheons, breakfasts , meetings

Industry/Entity Type

Catering

Requirements
Must have
• I have attached a copy of the text that what we want in the package, our logo, and i have also attached a catering package of another company to give you an idea what the finished product will be
Should not have
• It should not look identical to the example catering packages, these are for some inspiration we want our own design with the same type of look and feel

```html
<!DOCTYPE html>
<html lang="en">
<head>
<meta charset="utf-8">
<title>Meadowbrook Caterers – Party Menus</title>
<link href="https://fonts.googleapis.com/css2?family=Great+Vibes&family=Merriweather:wght@400&display=swap" rel="stylesheet">
<style>
  :root {
    --ink: #2b221d;
    --accent: #8f5128;
    --heading: #6b5a50;
    --sidebar-top: #e9dfd4;
    --sidebar-bottom: #dccbbb;
    --page: #ffffff;
    --page-shade: #f1ece7;
    --photo-fish: #8a7a6c;
    --photo-plate: #7a5a48;
    --photo-bread: #c9a77c;
    --photo-queso: #e0b460;
  }
  * { box-sizing: border-box; margin: 0; padding: 0; }
  html, body { width: 1200px; height: 927px; overflow: hidden; }
  body { background: var(--page); font-family: "Merriweather", Georgia, serif; color: var(--ink); }
  .menu-page {
    position: relative; width: 1200px; height: 927px; overflow: hidden;
    background: radial-gradient(ellipse at 60% 10%, var(--page) 40%, var(--page-shade) 100%);
  }
  .sidebar {
    position: absolute; left: 0; top: 0; width: 183px; height: 927px;
    background: linear-gradient(180deg, var(--sidebar-top), var(--page) 35%, var(--sidebar-bottom));
  }
  .brand {
    position: absolute; left: 28px; top: 30px; width: 140px;
    display: flex; flex-direction: column; align-items: flex-start; gap: 12px;
  }
  .brand-mark { width: 40px; height: 40px; background: var(--accent); border-radius: 50%; }
  .brand-name { font-size: 20px; line-height: 1.15; color: var(--ink); font-weight: 400; }
  .menu-column { position: absolute; top: 52px; }
  .menu-column--mingle { left: 197px; }
  .menu-column--office { left: 691px; }
  .menu-title {
    font-family: "Great Vibes", cursive; font-weight: 400; font-size: 46px;
    color: var(--heading); text-shadow: 2px 3px 4px rgba(0,0,0,.25);
    height: 72px; line-height: 60px;
  }
  .menu-list { list-style: none; margin-top: 8px; }
  .menu-list li { font-size: 17px; line-height: 36.4px; white-space: nowrap; }
  .menu-list li.note { color: var(--accent); }
  .menu-list li.note-wrap { white-space: normal; line-height: 24px; padding: 6px 0; width: 330px; }
  .photo { position: absolute; }
  .photo--fish { left: 208px; top: 658px; width: 286px; height: 189px;
    background: linear-gradient(135deg, var(--photo-fish), #d8c8b4 55%, #4a3a30);
    box-shadow: 2px 3px 8px rgba(0,0,0,.35); }
  .photo--plate { left: 506px; top: 544px; width: 153px; height: 194px;
    background: radial-gradient(circle at 55% 50%, #e8ddd0 0 30%, var(--photo-plate) 55%, #3c2a22);
    box-shadow: 2px 3px 8px rgba(0,0,0,.35); }
  .photo--bread { left: 515px; top: 739px; width: 200px; height: 200px; border-radius: 50%;
    background: radial-gradient(circle, #f3e6cf 0 40%, var(--photo-bread) 60%, #6e4a2c); }
  .photo--queso { left: 894px; top: 727px; width: 306px; height: 200px;
    border-top-left-radius: 150px 100px;
    background: radial-gradient(ellipse at 55% 35%, var(--photo-queso) 0 35%, #8a2c24 45%, #d9b56a 60%, #7c8f3a); }
</style>
</head>
<body>
<main class="menu-page">
  <aside class="sidebar">
    <div class="brand">
      <span class="brand-mark"></span>
      <span class="brand-name">Meadowbrook Caterers</span>
    </div>
  </aside>

  <section class="menu-column menu-column--mingle">
    <h2 class="menu-title">The Mix &amp; Mingle</h2>
    <ul class="menu-list">
      <li>Scallops Wrapped in Bacon</li>
      <li class="note">Shrimp Cocktail</li>
      <li>Thai Grilled Chicken Bites</li>
      <li class="note">Served with Steamed Wild Rice</li>
      <li>Marinated Flank Steak</li>
      <li class="note">Carved &amp; served with herb mayonnaise &amp; horseradish</li>
      <li>With fresh rolls &amp; Artisan bread</li>
      <li class="note">Aged Cheese Board</li>
      <li>Pepper Jack, Smoked Gouda, English Cheddar</li>
      <li class="note">Goat, Gorgonzola &amp; Aged Swiss</li>
      <li>Garnished with dried fruit &amp; nuts</li>
      <li class="note">Served with crackers</li>
      <li>Mediterranean Pasta Salad</li>
      <li class="note">Fresh Fruit &amp; Melon Display</li>
    </ul>
  </section>

  <section class="menu-column menu-column--office">
    <h2 class="menu-title">The Office Party</h2>
    <ul class="menu-list">
      <li>Grilled Marinated London Broil</li>
      <li class="note note-wrap">Carved &amp; served with horseradish &amp; port wine mushroom sauce</li>
      <li>Grilled Whole Mahi Mahi Display</li>
      <li class="note">Served with fruit salsa</li>
      <li>Southwest Twice Baked Potato Bites</li>
      <li class="note note-wrap">Stuffed with Scallions, Bacon, Cheese, Butter &amp; Sour cream</li>
      <li>Balsamic Fire Roasted Vegetable Medley</li>
      <li class="note">Fresh Baked Rolls &amp; Artisan Bread</li>
      <li>Served with Whipped Butter</li>
      <li class="note">Bite Sized Italian Sausage</li>
      <li>With Peppers &amp; Onions</li>
      <li class="note">With Condiments &amp; Fresh Baked Rolls</li>
      <li>Buffalo Drummies &amp; Wing Sections</li>
      <li class="note note-wrap">Served with Bleu Cheese Dressing, Celery &amp; Carrot Sticks</li>
      <li>Queso Dip</li>
      <li class="note">Served with Tortilla Chips</li>
    </ul>
  </section>

  <div class="photo photo--fish" role="img" aria-label="Photo of grilled fish fillet garnished with rosemary and orange"></div>
  <div class="photo photo--plate" role="img" aria-label="Photo of a plated dinner with shrimp, beets, green beans and potatoes"></div>
  <div class="photo photo--bread" role="img" aria-label="Photo of a basket of fresh baked rolls with butter"></div>
  <div class="photo photo--queso" role="img" aria-label="Photo of a bowl of queso dip with tortilla chips and peppers"></div>
</main>
</body>
</html>
```